Indy Film Production Company/Studio

We need a business card designed from an existing logo. We are a digital studio/production company that caters to creating genre entertainment, like Action, Horror, and martial arts. The card along with the logo will be used to Brand the company from letter heads to banners. The design will also be used for postcards and Brochures. It should be professional and masculine.
Updates

Thank you to all the designers who have participated. I'm narrowing down who it will be. Thank you again.

Target Market(s)

Investors, Networks, Producers, and actors

Industry/Entity Type

Film Production

Contact Information for Business Card

Teodoro Valbuena
Producer/Writer/Director
www.kestrelpicturehouse.example

Requirements
Must have
• Website address, Facebook icon and Twitter icon possibly in the back of the card.
Nice to have
• Logline of Company: Follow The Action.

```html
<!DOCTYPE html>
<html lang="en">
<head>
<meta charset="utf-8">
<title>Kestrel Picture House – Business Card</title>
<link rel="stylesheet" href="https://fonts.googleapis.com/css2?family=Open+Sans:wght@400;600;800&display=swap">
<style>
  :root {
    --stage: #3a332f;
    --card: #0d0d0d;
    --card-edge: #1a1a1a;
    --red: #e0232a;
    --white: #f2f2f2;
    --grey: #8a8a8a;
    --photo-light: #9a9a9a;
    --photo-dark: #1c1c1c;
  }
  * { margin: 0; padding: 0; box-sizing: border-box; }
  html, body { width: 1200px; height: 814px; overflow: hidden; }
  body {
    background: var(--stage);
    font-family: "Open Sans", Arial, sans-serif;
    position: relative;
  }
  .card {
    position: absolute;
    top: 252px;
    width: 520px;
    height: 297px;
    background: var(--card);
    border: 1px solid var(--card-edge);
    box-shadow: 0 6px 18px rgba(0,0,0,.45);
    overflow: hidden;
  }
  .card--front { left: 50px; }
  .card--back { left: 630px; }

  /* wordmark stand-in */
  .wordmark {
    display: flex;
    align-items: center;
    gap: 10px;
    color: var(--red);
    font-weight: 800;
    text-transform: uppercase;
    line-height: 1.05;
  }
  .wordmark__square { width: 16px; height: 16px; background: var(--red); flex: none; }

  /* front */
  .card--front .wordmark {
    position: absolute;
    left: 34px;
    top: 118px;
    font-size: 23px;
    width: 210px;
  }
  .divider {
    position: absolute;
    left: 262px;
    top: 70px;
    width: 1px;
    height: 160px;
    background: var(--grey);
  }
  .contact {
    position: absolute;
    left: 284px;
    top: 78px;
    color: var(--white);
  }
  .contact__name { color: var(--red); font-size: 17px; font-weight: 600; }
  .contact__role { font-size: 13px; margin-bottom: 12px; }
  .contact__row {
    display: flex;
    align-items: center;
    gap: 8px;
    font-size: 12px;
    margin-bottom: 6px;
    white-space: nowrap;
  }
  .contact__row svg { width: 12px; height: 12px; flex: none; }

  /* back */
  .social {
    position: absolute;
    left: 42px;
    top: 42px;
    display: flex;
    gap: 4px;
  }
  .social span { width: 20px; height: 20px; background: var(--red); }
  .camera-photo {
    position: absolute;
    right: 0;
    top: 0;
    width: 270px;
    height: 240px;
    background: radial-gradient(ellipse at 50% 45%, var(--photo-light) 0%, #4a4a4a 40%, var(--photo-dark) 75%, var(--card) 100%);
  }
  .card--back .wordmark {
    position: absolute;
    left: 42px;
    top: 188px;
    font-size: 22px;
    width: 230px;
  }
  .back-url {
    position: absolute;
    left: 42px;
    top: 250px;
    color: var(--white);
    font-size: 12px;
  }
</style>
</head>
<body>

<section class="card card--front">
  <div class="wordmark"><span class="wordmark__square"></span><span>Kestrel Picture House</span></div>
  <div class="divider"></div>
  <div class="contact">
    <p class="contact__name">Teodoro Valbuena</p>
    <p class="contact__role">Producer/Writer/Director</p>
    <p class="contact__row">
      <svg viewBox="0 0 12 12"><path fill="#e0232a" d="M2.5 1 4.3 1l.8 2.6-1.2 1a6 6 0 0 0 2.5 2.5l1-1.2 2.6.8v1.8c0 .6-.5 1-1 1A8.5 8.5 0 0 1 1.5 2c0-.5.4-1 1-1z"/></svg>
      555 014 2290
    </p>
    <p class="contact__row">
      <svg viewBox="0 0 12 12"><rect x="1" y="2.5" width="10" height="7" fill="#e0232a"/><path d="M1 2.5 6 6.5l5-4" fill="none" stroke="#0d0d0d" stroke-width="1"/></svg>
      hello@kestrelpicturehouse.example
    </p>
    <p class="contact__row">
      <svg viewBox="0 0 12 12"><circle cx="6" cy="6" r="5" fill="#e0232a"/><path d="M1 6h10M6 1c-2.5 3-2.5 7 0 10M6 1c2.5 3 2.5 7 0 10" fill="none" stroke="#0d0d0d" stroke-width=".8"/></svg>
      www.kestrelpicturehouse.example
    </p>
  </div>
</section>

<section class="card card--back">
  <div class="social" aria-label="Social media"><span></span><span></span></div>
  <div class="camera-photo" role="img" aria-label="Photograph of a professional cinema camera rig"></div>
  <div class="wordmark"><span class="wordmark__square"></span><span>Kestrel Picture House</span></div>
  <p class="back-url">www.kestrelpicturehouse.example</p>
</section>

</body>
</html>
```